Brookvale Building Company - advertisement poster

I am looking to print some canvas signs to advertise my general contracting company, Brookvale Building Company. The sign will measure 6' long x 3' high so the size should match that ratio. I already have a logo icon, which is the Letter 'B' and some trees that I would like to incorporate, see attached. I would also like the to have the following information listed:
1) phone number: 831-555-0172
2) email: brookvalebuildingcompany@mailnest.example
3) website: brookvalebuildingcompany.example
4) Lic#4826130
5) I want to use this text: "BUILD WITH THE B-CREW!"

The ad should be relatively simple and clean. Black and Green are my company colors. I am open to creative ideas!

Target Market(s)

People looking to renovate their homes

Industry/Entity Type

Construction

Colors
59FF00
82FF00
B8FF75
E3FFCB
F4FFEA

Requirements
Must have
• Must have my company logo
Should not have
• No photos or complex graphics

```html
<!DOCTYPE html>
<html lang="en">
<head>
<meta charset="utf-8">
<title>Brookvale Building Company – Sign</title>
<link rel="stylesheet" href="https://fonts.googleapis.com/css2?family=Archivo+Black&family=Montserrat:wght@600;700&display=swap">
<style>
  :root {
    --sign-black: #231f20;
    --brand-green: #6cb644;
    --ink-dark: #1d1a1b;
    --name-white: #ffffff;
    --soft-green: #b8e08f;
    --backdrop: #e6e8ea;
  }
  * { margin: 0; padding: 0; box-sizing: border-box; }
  html, body {
    width: 1200px;
    height: 800px;
    overflow: hidden;
    background: var(--backdrop);
  }
  .canvas {
    position: relative;
    width: 1200px;
    height: 800px;
  }
  .sign {
    position: absolute;
    left: 30px;
    top: 115px;
    width: 1140px;
    height: 570px;
    background: var(--sign-black);
    overflow: hidden;
  }
  .headline {
    position: absolute;
    left: 62px;
    top: 140px;
    color: var(--brand-green);
    font-family: "Archivo Black", "Arial Black", sans-serif;
    line-height: 1;
  }
  .headline__lead {
    display: block;
    font-size: 66px;
    letter-spacing: 1px;
  }
  .headline__crew {
    display: block;
    margin-top: 6px;
    font-size: 124px;
    letter-spacing: -2px;
  }
  .brand {
    position: absolute;
    right: 60px;
    top: 150px;
    width: 340px;
    display: flex;
    flex-direction: column;
    align-items: center;
  }
  .brand__mark {
    width: 76px;
    height: 76px;
    background: var(--brand-green);
    margin-bottom: 18px;
  }
  .brand-name {
    text-align: center;
    color: var(--name-white);
    font-family: "Archivo Black", "Arial Black", sans-serif;
    text-transform: uppercase;
    line-height: 1.05;
  }
  .brand-name__main {
    display: block;
    font-size: 46px;
    letter-spacing: 1px;
  }
  .brand-name__sub {
    display: block;
    margin-top: 6px;
    font-size: 19px;
    letter-spacing: 4px;
  }
  .details {
    position: absolute;
    right: 60px;
    bottom: 128px;
    display: flex;
    gap: 28px;
    color: var(--soft-green);
    font-family: "Montserrat", "Helvetica", sans-serif;
    font-weight: 600;
    font-size: 18px;
    letter-spacing: 0.5px;
  }
  .contact-band {
    position: absolute;
    left: 0;
    bottom: 0;
    width: 100%;
    height: 104px;
    background: var(--brand-green);
    display: flex;
    align-items: center;
    padding: 0 44px;
    color: var(--ink-dark);
  }
  .contact-phone {
    display: flex;
    align-items: center;
    gap: 22px;
    font-family: "Archivo Black", "Arial Black", sans-serif;
    font-size: 58px;
    letter-spacing: 1px;
  }
  .contact-web {
    margin-left: auto;
    display: flex;
    align-items: center;
    gap: 12px;
    font-family: "Montserrat", "Helvetica", sans-serif;
    font-weight: 700;
    font-size: 24px;
  }
  .icon { flex: none; }
</style>
</head>
<body>
  <main class="canvas">
    <section class="sign" aria-label="Brookvale Building Company advertisement">
      <h1 class="headline">
        <span class="headline__lead">Build with the</span>
        <span class="headline__crew">B-CREW!</span>
      </h1>

      <div class="brand">
        <div class="brand__mark" role="img" aria-label="Brookvale Building Company logo icon"></div>
        <p class="brand-name">
          <span class="brand-name__main">Brookvale</span>
          <span class="brand-name__sub">Building Company</span>
        </p>
      </div>

      <p class="details">
        <span class="details__email">brookvalebuildingcompany@mailnest.example</span>
        <span class="details__license">Lic#4826130</span>
      </p>

      <footer class="contact-band">
        <div class="contact-phone">
          <svg class="icon icon--phone" width="56" height="56" viewBox="0 0 56 56" aria-hidden="true">
            <circle cx="28" cy="28" r="25" fill="none" stroke="var(--ink-dark)" stroke-width="3"/>
            <path d="M19 17c2-1 3-1 4 1l3 5c1 2 0 3-1 4l-1 1c1 3 4 6 7 7l1-1c1-1 2-2 4-1l5 3c2 1 2 2 1 4l-2 2c-2 2-6 2-10 0-5-3-10-8-13-13-2-4-2-8 0-10z" fill="var(--ink-dark)"/>
            <path d="M31 16a9 9 0 0 1 9 9M31 11a14 14 0 0 1 14 14" fill="none" stroke="var(--ink-dark)" stroke-width="2.5" stroke-linecap="round"/>
          </svg>
          <span>831.555.0172</span>
        </div>
        <div class="contact-web">
          <svg class="icon icon--globe" width="26" height="26" viewBox="0 0 26 26" aria-hidden="true">
            <g fill="none" stroke="var(--ink-dark)" stroke-width="2">
              <circle cx="13" cy="13" r="11"/>
              <ellipse cx="13" cy="13" rx="5" ry="11"/>
              <line x1="2" y1="13" x2="24" y2="13"/>
              <line x1="4" y1="7.5" x2="22" y2="7.5"/>
              <line x1="4" y1="18.5" x2="22" y2="18.5"/>
            </g>
          </svg>
          <span>BrookvaleBuildingCompany.example</span>
        </div>
      </footer>
    </section>
  </main>
</body>
</html>
```